New florist business website design

Number 1 want is an easy to navigate & check out website
Needs to be beautiful and eye catching as well.
This is an online only business (no shop front)
Rustic and blush pinks, neutrals, woods, leaves
Customers need to be able to go onto my website, select something they want to buy but have the option to use a drop down box to change colours of the flowers, or add notes to make changes to the arrangement

Industry/Entity Type

Florist

Coding

Coded - Design and coding required

Number of Pages Required

5+ page

Colors
f9d9e8
fff2ec
fffefc

Requirements
Must have
• Drop down menu to take you to other pages for Arrangements, bouquets, everlasting arrangements, gifts, contact
Be able to purchase and “add to basket”
Checkout page
Nice to have
• Be able to add my own photos once I’ve taken new ones
Should not have
• Tacky images or clip art

```html
<!DOCTYPE html>
<html lang="en">
<head>
<meta charset="utf-8">
<title>Petal &amp; Fern — Florist</title>
<link href="https://fonts.googleapis.com/css2?family=Playfair+Display:wght@400;700&family=Great+Vibes&family=Lato:wght@400;700&display=swap" rel="stylesheet">
<style>
:root{
  --blush:#fcf0f2;
  --blush-deep:#f9d9e8;
  --cream:#fff2ec;
  --paper:#fffefc;
  --ink:#2c2c2c;
  --muted:#555;
  --rose:#d9a1a8;
  --wood:#5b3a29;
  --leaf:#4c6b3c;
  --footer:#3b3b3b;
  --serif:'Playfair Display',serif;
  --script:'Great Vibes',cursive;
  --sans:'Lato',sans-serif;
}
*{margin:0;padding:0;box-sizing:border-box}
html,body{width:1200px;height:4688px;overflow:hidden}
body{position:relative;background:var(--paper);font-family:var(--sans);color:var(--ink)}
.abs{position:absolute}
.band{position:absolute;left:0;width:1200px}
.center{text-align:center;left:0;width:1200px}
.script{font-family:var(--script);font-size:44px;color:var(--ink);line-height:1}
.title{font-family:var(--serif);font-size:32px;letter-spacing:.5px;text-transform:uppercase;line-height:1}
.btn{position:absolute;font-family:var(--serif);font-size:14px;display:flex;align-items:center;justify-content:center;border:2px solid var(--ink);color:var(--ink);background:transparent}
.btn.light{border-color:#fff;color:#fff}
.header{top:0;height:110px;background:var(--blush)}
.topbar{top:17px;font-size:12px;font-family:var(--serif);color:var(--muted)}
.nav{top:56px;font-family:var(--serif);font-size:15px;color:#444}
.nav span{position:absolute;white-space:nowrap}
.logo-disc{left:520px;top:-70px;width:160px;height:225px;border-radius:0 0 80px 80px;background:var(--blush)}
.logo-ring{left:532px;top:0;width:136px;height:136px;border-radius:50%;border:1px solid #e6cfd4}
.logo-name{left:520px;top:50px;width:160px;text-align:center;font-family:var(--serif);font-size:22px;color:#555}
.hero{top:110px;height:537px;background:linear-gradient(90deg,#8a4a52 0%,#5b3a29 25%,#6b4530 50%,#5a3a28 72%,#3f5c33 100%)}
.arrow-round{position:absolute;width:38px;height:38px;border-radius:50%;background:rgba(255,255,255,.8);display:flex;align-items:center;justify-content:center}
.feature{position:absolute;width:300px;text-align:center}
.feature h3{font-family:var(--serif);font-weight:400;font-size:16px;text-transform:uppercase;color:#333}
.feature p{font-size:13px;line-height:22px;color:#444;margin-top:22px}
.card{position:absolute;width:235px;height:304px;background:#fff;box-shadow:0 1px 6px rgba(0,0,0,.08)}
.card .img{position:absolute;left:0;top:0;width:235px;height:222px;background:#f5f5f5}
.card .bloom{position:absolute;left:62px;top:30px;width:110px;height:150px;border-radius:50% 50% 45% 45%}
.card .name{position:absolute;left:17px;top:240px;font-size:12px;font-weight:700}
.card .price{position:absolute;right:17px;top:241px;font-size:11px;color:#666}
.card .line{position:absolute;left:0;right:0;top:268px;border-top:1px solid #eee}
.card .ship{position:absolute;left:17px;top:283px;font-size:9px;font-weight:700;color:#555;display:flex;align-items:center;gap:8px}
.card .fav{position:absolute;right:17px;top:277px;width:22px;height:22px;border-radius:50%;border:1px solid #888;display:flex;align-items:center;justify-content:center}
.chev{position:absolute;width:38px;height:38px;border-radius:50%;background:#fff;box-shadow:0 1px 5px rgba(0,0,0,.15);display:flex;align-items:center;justify-content:center}
.framed{position:absolute;border:3px solid #333;padding:6px;background:#fff}
.framed div{width:100%;height:100%}
.footer{top:4280px;height:408px;background:var(--footer);color:#ddd}
.footer h4{position:absolute;font-size:17px;font-weight:700;color:#fff}
.footer ul{position:absolute;list-style:none;font-size:12px;line-height:22.4px;color:#ccc}
.footer li::before{content:"»";margin-right:10px;color:#aaa}
.pay{position:absolute;top:4621px;width:44px;height:28px;border-radius:3px}
</style>
</head>
<body>

<header class="band header">
  <div class="abs topbar" style="left:215px">&#9990; Call us : +1 555 214 7730</div>
  <div class="abs topbar" style="left:870px">&#9711; My account</div>
  <svg class="abs" style="left:1010px;top:12px" width="30" height="26" viewBox="0 0 30 26" aria-hidden="true"><path d="M3 9h16l-2 14H5z" fill="none" stroke="#555" stroke-width="1.4"/><path d="M7 9a4 4 0 0 1 8 0" fill="none" stroke="#555" stroke-width="1.4"/><circle cx="23" cy="8" r="6" fill="#f3c6cd"/><text x="23" y="11" font-size="8" text-anchor="middle" fill="#333" font-family="Lato">1</text></svg>
  <nav class="nav">
    <span style="left:217px;top:56px">Home</span>
    <span style="left:292px;top:56px">Arrangements &#8964;</span>
    <span style="left:425px;top:56px">Bouquets &#8964;</span>
    <span style="left:707px;top:56px">Everlasting arrangements &#8964;</span>
    <span style="left:919px;top:56px">Gifts &#8964;</span>
    <span style="left:987px;top:56px">Contact</span>
  </nav>
  <div class="abs" style="left:205px;top:80px;width:837px;border-top:1px solid #d8c4c8"></div>
  <div class="abs" style="left:233px;top:77px;width:0;height:0;border-left:5px solid transparent;border-right:5px solid transparent;border-bottom:6px solid #999"></div>
</header>
<div class="abs logo-disc"></div>
<div class="abs logo-ring"></div>
<div class="abs logo-name">Petal &amp; Fern</div>

<section class="band hero" role="img" aria-label="Overhead view of hands arranging a bouquet on a wooden table surrounded by fresh flowers, twine and scissors"></section>
<div class="abs center script" style="top:290px;color:#fff;font-size:58px">Welcome to</div>
<div class="abs center" style="top:362px;font-family:var(--serif);font-size:48px;color:#fff">PERFECT BOUQUET</div>
<div class="btn" style="left:459px;top:433px;width:134px;height:42px;background:var(--cream);border-color:var(--cream)">Shop now</div>
<div class="btn light" style="left:605px;top:433px;width:134px;height:42px">Read more &#10230;</div>
<div class="arrow-round" style="left:36px;top:359px"><svg width="10" height="14"><path d="M8 1 2 7l6 6" stroke="#555" fill="none" stroke-width="2"/></svg></div>
<div class="arrow-round" style="left:1124px;top:359px"><svg width="10" height="14"><path d="M2 1l6 6-6 6" stroke="#555" fill="none" stroke-width="2"/></svg></div>

<div class="feature" style="left:123px;top:705px">
  <svg width="70" height="70" viewBox="0 0 70 70" aria-hidden="true"><g fill="none" stroke="#333" stroke-width="2"><circle cx="35" cy="19" r="11"/><circle cx="50" cy="30" r="11"/><circle cx="45" cy="48" r="11"/><circle cx="25" cy="48" r="11"/><circle cx="20" cy="30" r="11"/><circle cx="35" cy="35" r="6"/></g></svg>
  <h3 style="margin-top:22px">Ready to be impressed</h3>
  <p>Lorem ipsum dolor sit amet, consecte tur<br>adipiscing elitin uta</p>
</div>
<div class="feature" style="left:450px;top:700px">
  <svg width="76" height="76" viewBox="0 0 76 76" aria-hidden="true"><g fill="none" stroke="#333" stroke-width="2"><circle cx="38" cy="16" r="9"/><circle cx="52" cy="26" r="9"/><circle cx="26" cy="28" r="9"/><circle cx="42" cy="36" r="9"/><path d="M30 42 12 66l8 4 20-24M20 60l8 4"/></g></svg>
  <h3 style="margin-top:22px">Powerful solutions</h3>
  <p>Lorem ipsum dolor sit amet, consecte tur<br>adipiscing elitin uta</p>
</div>
<div class="feature" style="left:775px;top:702px">
  <svg width="74" height="74" viewBox="0 0 74 74" aria-hidden="true"><g fill="none" stroke="#333" stroke-width="2"><path d="M37 70V30"/><path d="M37 50C20 52 8 40 6 20c18 2 30 12 31 30z"/><path d="M37 50c17 2 29-10 31-30-18 2-30 12-31 30z"/><circle cx="37" cy="22" r="10"/></g></svg>
  <h3 style="margin-top:22px">Leaders of tomorrow</h3>
  <p>Lorem ipsum dolor sit amet, consecte tur<br>adipiscing elitin uta</p>
</div>

<section class="band" style="top:983px;height:1288px;background:var(--blush)"></section>
<div class="abs center script" style="top:1066px">Wonderful gift</div>
<div class="abs center title" style="top:1137px">Our wonderful arrangements</div>

<div class="chev" style="left:27px;top:1350px"><svg width="10" height="14"><path d="M8 1 2 7l6 6" stroke="#222" fill="none" stroke-width="2.4"/></svg></div>
<div class="chev" style="left:1135px;top:1350px"><svg width="10" height="14"><path d="M2 1l6 6-6 6" stroke="#222" fill="none" stroke-width="2.4"/></svg></div>

<div class="card" style="left:102px;top:1207px"><div class="img"><div class="bloom" role="img" aria-label="White and green mixed bouquet" style="background:radial-gradient(circle,#f4f2ea,#b9c6a6)"></div></div><div class="name">PRODUCT TITLE</div><div class="price">$50.00</div><div class="line"></div><div class="ship">&#9951; SAME DAY DELIVERY</div><div class="fav"><svg width="11" height="10"><path d="M5.5 9 1 4.5a2.2 2.2 0 0 1 4.5-3 2.2 2.2 0 0 1 4.5 3z" fill="none" stroke="#666"/></svg></div></div>
<div class="card" style="left:355px;top:1207px"><div class="img"><div class="bloom" role="img" aria-label="Red rose bouquet" style="background:radial-gradient(circle,#c4161c,#7a1d1d 60%,#4d6b3a)"></div></div><div class="name">PRODUCT TITLE</div><div class="price">$50.00</div><div class="line"></div><div class="ship">&#9951; SAME DAY DELIVERY</div><div class="fav"><svg width="11" height="10"><path d="M5.5 9 1 4.5a2.2 2.2 0 0 1 4.5-3 2.2 2.2 0 0 1 4.5 3z" fill="none" stroke="#666"/></svg></div></div>
<div class="card" style="left:608px;top:1207px"><div class="img"><div class="bloom" role="img" aria-label="Purple and pink mixed bouquet" style="background:radial-gradient(circle,#c23a8a,#7b3e8f 60%,#5a7a3a)"></div></div><div class="name">PRODUCT TITLE</div><div class="price">$50.00</div><div class="line"></div><div class="ship">&#9951; SAME DAY DELIVERY</div><div class="fav"><svg width="11" height="10"><path d="M5.5 9 1 4.5a2.2 2.2 0 0 1 4.5-3 2.2 2.2 0 0 1 4.5 3z" fill="none" stroke="#666"/></svg></div></div>
<div class="card" style="left:862px;top:1207px"><div class="img"><div class="bloom" role="img" aria-label="Pink and white tulip bouquet" style="background:radial-gradient(circle,#f1c4da,#e8e1ea 55%,#7fa05a)"></div></div><div class="name">PRODUCT TITLE</div><div class="price">$50.00</div><div class="line"></div><div class="ship">&#9951; SAME DAY DELIVERY</div><div class="fav"><svg width="11" height="10"><path d="M5.5 9 1 4.5a2.2 2.2 0 0 1 4.5-3 2.2 2.2 0 0 1 4.5 3z" fill="none" stroke="#666"/></svg></div></div>

<div class="abs" role="img" aria-label="Line drawing of a flowering branch" style="left:18px;top:1610px;width:305px;height:265px;background:radial-gradient(ellipse at 40% 40%,rgba(160,140,140,.18),transparent 70%)"></div>
<div class="framed" style="left:523px;top:1659px;width:573px;height:513px"><div role="img" aria-label="Florist holding a large wrapped bouquet of roses, carnations and dried wheat" style="background:linear-gradient(135deg,#a89a8a,#c58aa0 40%,#6e6a74 70%,#5c6a4a)"></div></div>
<div class="abs" role="img" aria-label="Soft watercolour blush flowers" style="left:1020px;top:2080px;width:180px;height:120px;background:radial-gradient(ellipse,rgba(236,190,190,.55),transparent 70%)"></div>
<div class="abs" style="left:111px;top:1717px;width:537px;height:401px;background:#fff;box-shadow:0 2px 10px rgba(0,0,0,.06)"></div>
<div class="abs script" style="left:111px;width:537px;text-align:center;top:1764px">Wonderful gift</div>
<div class="abs title" style="left:111px;width:537px;text-align:center;top:1833px;font-size:30px">A perfect spot</div>
<p class="abs" style="left:152px;width:455px;top:1884px;text-align:center;font-size:13px;line-height:22.5px;color:#444">Lorem ipsum dolor sit amet, consectetur adipiscing elit, sed do eiusmod tempor incididunt ut labore et dolore magna aliqua. Ut enim ad minim veniam, quis nostrud exercitation ullamco laboris nisi ut aliquip ex ea commodo consequat. Duis aute irure dolor in reprehenderit in voluptate velit esse cillum dolore eu fugiat</p>
<div class="btn" style="left:313px;top:2019px;width:133px;height:41px">Read more &#10230;</div>

<section class="band" role="img" aria-label="Smiling florist in a striped top arranging flowers in a shop" style="top:2271px;height:344px;background:linear-gradient(90deg,#3d4a33,#6a6155 30%,#8a7f77 55%,#5c5a4e 80%,#3b4a30)"></section>
<div class="band" style="top:2271px;height:344px;background:rgba(40,30,30,.35)"></div>
<div class="abs" style="left:18px;top:2287px;width:1164px;height:313px;border:2px solid #fff"></div>
<div class="abs center script" style="top:2350px;color:#fff">For flower lovers</div>
<div class="abs center title" style="top:2421px;color:#fff;font-size:30px">Perfect choice</div>
<div class="btn light" style="left:532px;top:2478px;width:134px;height:42px">Read more &#10230;</div>

<section class="band" style="top:2615px;height:1665px;background:var(--blush)"></section>
<div class="framed" style="left:109px;top:2720px;width:310px;height:452px"><div role="img" aria-label="Hands holding a wrapped bouquet of pink roses and lilac" style="background:linear-gradient(160deg,#8aa07a,#c9a9c2 45%,#e6dfe4 75%,#b7b9c6)"></div></div>
<div class="framed" style="left:446px;top:2720px;width:306px;height:212px"><div role="img" aria-label="Bride holding a peach and pink rose bouquet" style="background:linear-gradient(135deg,#e9e4e2,#ec9d8d 45%,#f2c5bf 70%,#e6e2e0)"></div></div>
<div class="framed" style="left:446px;top:2959px;width:306px;height:213px"><div role="img" aria-label="Close view of colourful chrysanthemums" style="background:linear-gradient(135deg,#d8325a,#f08a2e 35%,#c43d8c 60%,#e85a3a 80%,#9b2d5c)"></div></div>
<div class="framed" style="left:779px;top:2720px;width:310px;height:452px"><div role="img" aria-label="Florist handing over a boxed flower arrangement in a paper bag" style="background:linear-gradient(170deg,#d4c7b4,#a3b38a 40%,#f0ede6 65%,#8b6a4f)"></div></div>
<div class="btn" style="left:532px;top:3203px;width:134px;height:42px">View more &#10230;</div>

<div class="abs center script" style="top:3330px">Wonderful gift</div>
<div class="abs center title" style="top:3400px">Best seller</div>
<div class="chev" style="left:27px;top:3610px"><svg width="10" height="14"><path d="M8 1 2 7l6 6" stroke="#222" fill="none" stroke-width="2.4"/></svg></div>
<div class="chev" style="left:1135px;top:3610px"><svg width="10" height="14"><path d="M2 1l6 6-6 6" stroke="#222" fill="none" stroke-width="2.4"/></svg></div>

<div class="card" style="left:102px;top:3469px"><div class="img"><div class="bloom" role="img" aria-label="Bright mixed bouquet with lilies and roses" style="background:radial-gradient(circle,#f28a2a,#c2287a 55%,#4f7a3a)"></div></div><div class="name">PRODUCT TITLE</div><div class="price">$50.00</div><div class="line"></div><div class="ship">&#9951; SAME DAY DELIVERY</div><div class="fav"><svg width="11" height="10"><path d="M5.5 9 1 4.5a2.2 2.2 0 0 1 4.5-3 2.2 2.2 0 0 1 4.5 3z" fill="none" stroke="#666"/></svg></div></div>
<div class="card" style="left:355px;top:3469px"><div class="img"><div class="bloom" role="img" aria-label="Cream and blush rose bouquet" style="background:radial-gradient(circle,#f6ece4,#e7c7c0 55%,#7a8a66)"></div></div><div class="name">PRODUCT TITLE</div><div class="price">$50.00</div><div class="line"></div><div class="ship">&#9951; SAME DAY DELIVERY</div><div class="fav"><svg width="11" height="10"><path d="M5.5 9 1 4.5a2.2 2.2 0 0 1 4.5-3 2.2 2.2 0 0 1 4.5 3z" fill="none" stroke="#666"/></svg></div></div>
<div class="card" style="left:608px;top:3469px"><div class="img"><div class="bloom" role="img" aria-label="Pink rose and white bloom bouquet" style="background:radial-gradient(circle,#ee9fb4,#f4f0ec 55%,#3f6b35)"></div></div><div class="name">PRODUCT TITLE</div><div class="price">$50.00</div><div class="line"></div><div class="ship">&#9951; SAME DAY DELIVERY</div><div class="fav"><svg width="11" height="10"><path d="M5.5 9 1 4.5a2.2 2.2 0 0 1 4.5-3 2.2 2.2 0 0 1 4.5 3z" fill="none" stroke="#666"/></svg></div></div>
<div class="card" style="left:862px;top:3469px"><div class="img"><div class="bloom" role="img" aria-label="Yellow and orange gerbera bouquet" style="background:radial-gradient(circle,#f7c53a,#ef8a2a 55%,#5a7a3a)"></div></div><div class="name">PRODUCT TITLE</div><div class="price">$50.00</div><div class="line"></div><div class="ship">&#9951; SAME DAY DELIVERY</div><div class="fav"><svg width="11" height="10"><path d="M5.5 9 1 4.5a2.2 2.2 0 0 1 4.5-3 2.2 2.2 0 0 1 4.5 3z" fill="none" stroke="#666"/></svg></div></div>

<div class="abs" role="img" aria-label="Soft watercolour blush flowers" style="left:40px;top:3780px;width:150px;height:150px;background:radial-gradient(ellipse,rgba(236,190,195,.55),transparent 70%)"></div>
<div class="abs" role="img" aria-label="Soft watercolour blush flowers" style="left:1010px;top:4110px;width:170px;height:160px;background:radial-gradient(ellipse,rgba(236,190,195,.55),transparent 70%)"></div>
<div class="abs center script" style="top:3908px">For flower lovers</div>
<div class="abs center title" style="top:3964px">Our happy customers</div>
<p class="abs" style="left:286px;width:628px;top:4021px;text-align:center;font-style:italic;font-size:13px;line-height:23px;color:#444">“Lorem ipsum dolor sit amet, consectetur adipiscing elit, sed do eiusmod tempor incididunt ut labore et dolore magna aliqua. Ut enim ad minim veniam, quis nostrud exercitation ullamco laboris nisi ut aliquip ex ea commodo consequat. Duis aute irure dolor in reprehenderit in voluptate velit esse cillum dolore eu fugiat nulla pariatur. Excepteur sint occaecat cupidatat non proident, sunt in culpa qui officia deserunt mollit anim id est laborum.”</p>
<div class="abs center" style="top:4164px;font-size:14px;font-weight:700">Clara Wendell</div>
<svg class="abs" style="left:112px;top:4040px" width="24" height="42" aria-hidden="true"><path d="M22 2 3 21l19 19" stroke="#333" fill="none" stroke-width="2"/></svg>
<svg class="abs" style="left:1064px;top:4040px" width="24" height="42" aria-hidden="true"><path d="M2 2l19 19L2 40" stroke="#333" fill="none" stroke-width="2"/></svg>

<footer class="band footer">
  <h4 style="left:109px;top:70px">Product info</h4>
  <ul style="left:109px;top:114px"><li>Payment method</li><li>Faq</li><li>Shipping &amp; Delivery</li><li>Refunds &amp; Return policy</li><li>Truck your Order</li></ul>
  <h4 style="left:362px;top:70px">Quick Links</h4>
  <ul style="left:362px;top:114px"><li>Home</li><li>About</li><li>Product</li><li>Reviews</li><li>Contact us</li></ul>
  <h4 style="left:563px;top:70px">Contact info</h4>
  <div class="abs" style="left:563px;top:116px;font-size:12px;line-height:22.4px;color:#ccc;width:240px">
    <div style="display:flex;gap:14px"><span>&#9906;</span><span>123, Lorem ipsum dolor sit<br>amet, consectetur</span></div>
    <div style="margin-top:22px">&#9990;&nbsp;&nbsp;&nbsp;Phone : +1 555 214 7730</div>
    <div>&#9993;&nbsp;&nbsp;&nbsp;Email : hello@petalfern.com</div>
  </div>
  <h4 style="left:825px;top:70px">Newsletter</h4>
  <div class="abs" style="left:827px;top:121px;width:262px;height:44px;background:#4a4a4a;font-size:12px;color:#aaa;padding:14px 22px">Email address</div>
  <div class="abs" style="left:827px;top:180px;width:129px;height:40px;background:#fff;color:#222;font-size:12px;font-weight:700;display:flex;align-items:center;justify-content:center">SUBSCRIBE</div>
  <div class="abs center" style="top:292px;font-size:14px;color:#fff">&#169; Copyrights 2021 Company name | All Rights Reserved</div>
</footer>
<div class="pay" style="left:426px;background:#e8e8ea"></div>
<div class="pay" style="left:487px;background:#f2f2f2"></div>
<div class="pay" style="left:546px;background:#6f8fc4"></div>
<div class="pay" style="left:606px;background:#e6edf6"></div>
<div class="pay" style="left:666px;background:#d8d8d8"></div>
<div class="pay" style="left:726px;background:#2b2b2b;border:1px solid #777"></div>

</body>
</html>
```